Brochure for a civil enineering company in A4 format

I need a brochure design for our company TIRO Engineering S.r.l.. We are an engineering consultant company. Our main clients are from the infrastructure industry (geotechnical and underground sectors mainly).
We are looking for a 2 pages (4 faces) fold out design with a glued pocket where we can put individual data sheets.
I need A4 format pages.

Target Market(s)

We are an engineering consultant company. Our main clients are from the infrastructure industry (geotechnical and underground sectors mainly).

Industry/Entity Type

Civil Engineer

Font styles to use
Sans Serif

Requirements
Must have
• Overall: 2 pages in A4 format
Essential style. Bright and modern appearance.
Glued pocket
Logo integrated in a picture on the pocket where I would like to insert a slogan (… tiro engineering … reliable solutions …)
Attached are selected images which the designer can use and edit at their own discretion.
Some advice in the following (anyway designers are free to provide their solutions):
Outer sheets:
Front page with name, logo. It could be nice to have the “m” of the logo integrated in a pictures, also a modified picture (I mean modify one of the attached pictures) so to create a general image and do not tie the cover to a specific job.
Back page: offices address and contact email address. Nice to have one space for a slogan.
Inner sheet: text that I upload in the file “inside-sheets”, possibly with pictures on each sheet. In the right faces insert the glued pocket. On this pages insert the section OUR EXPERIENCE ….with a space for a picture of our team.
Nice to have
• Clean and essential design.
Pictures choosing from the atteched ones. Pictures could be modified in a very light manner to make them a general idea of the work ( I mean geotechnical world) without to be immediately linked to a specific site.
Should not have
• excessive frills

```html
<!DOCTYPE html>
<html lang="en">
<head>
<meta charset="utf-8">
<title>TIRO Engineering – Brochure Cover</title>
<link rel="stylesheet" href="https://fonts.googleapis.com/css2?family=Urbanist:wght@300;400;800&display=swap">
<style>
  :root {
    --backdrop: #e9e9e9;
    --cover-black: #050505;
    --tunnel-grey: #6d6a68;
    --tunnel-light: #d9d6d0;
    --rock-red: #4a1512;
    --ink-white: #ffffff;
    --ink-soft: #cfcfcf;
  }
  * { box-sizing: border-box; margin: 0; padding: 0; }
  html, body {
    width: 900px;
    height: 1200px;
    overflow: hidden;
    background: var(--backdrop);
    font-family: "Urbanist", sans-serif;
  }
  .canvas {
    position: relative;
    width: 900px;
    height: 1200px;
  }
  .cover {
    position: absolute;
    left: 70px;
    top: 62px;
    width: 760px;
    height: 1075px;
    background: var(--cover-black);
    overflow: hidden;
    box-shadow: 0 8px 24px rgba(0,0,0,0.18);
  }
  .cover-photo {
    position: absolute;
    inset: 0 0 auto 0;
    height: 800px;
    background:
      radial-gradient(ellipse 150px 190px at 68% 46%, var(--tunnel-light) 0%, rgba(150,146,140,0.75) 35%, rgba(40,38,37,0) 100%),
      radial-gradient(ellipse 360px 420px at 62% 42%, rgba(109,106,104,0.55) 0%, rgba(20,20,20,0) 75%),
      radial-gradient(ellipse 260px 360px at 8% 70%, rgba(74,21,18,0.75) 0%, rgba(5,5,5,0) 80%),
      linear-gradient(180deg, #141414 0%, #1c1b1a 55%, var(--cover-black) 100%);
  }
  .cover-photo::after {
    content: "";
    position: absolute;
    inset: auto 0 0 0;
    height: 260px;
    background: linear-gradient(180deg, rgba(5,5,5,0) 0%, var(--cover-black) 100%);
  }
  .brand {
    position: absolute;
    top: 640px;
    left: 0;
    right: 0;
    text-align: center;
    color: var(--ink-white);
  }
  .brand-name {
    display: inline-flex;
    align-items: center;
    gap: 14px;
    font-weight: 800;
    font-size: 76px;
    line-height: 1;
    letter-spacing: 1px;
  }
  .brand-mark {
    width: 22px;
    height: 22px;
    border-radius: 50%;
    background: var(--ink-white);
  }
  .brand-tagline {
    margin-top: 6px;
    font-weight: 400;
    font-size: 9px;
    letter-spacing: 3.5px;
    text-transform: uppercase;
    color: var(--ink-soft);
  }
  .slogan {
    position: absolute;
    top: 762px;
    left: 0;
    right: 0;
    text-align: center;
    color: var(--ink-white);
    line-height: 1.05;
  }
  .slogan-line-one {
    font-size: 34px;
    font-weight: 300;
  }
  .slogan-line-two {
    font-size: 56px;
    font-weight: 300;
  }
  .slogan strong { font-weight: 800; }
  .slogan-rule {
    display: block;
    width: 72px;
    height: 2px;
    margin: 22px auto 0;
    background: var(--ink-white);
  }
  .website {
    position: absolute;
    top: 930px;
    left: 0;
    right: 0;
    text-align: center;
    font-size: 15px;
    font-weight: 400;
    letter-spacing: 6px;
    color: var(--ink-soft);
  }
</style>
</head>
<body>
  <main class="canvas">
    <section class="cover">
      <div class="cover-photo" role="img" aria-label="Photograph of an underground tunnel under construction with steel arch ribs, a bright opening in the distance and a worker silhouetted on the wet floor"></div>

      <div class="brand">
        <div class="brand-name"><span class="brand-mark"></span>tiro</div>
        <p class="brand-tagline">tiro engineering · reliable solutions</p>
      </div>

      <div class="slogan">
        <p class="slogan-line-one">We work to <strong>mitigate risk</strong> and</p>
        <p class="slogan-line-two"><strong>reduce</strong> uncertainty</p>
        <span class="slogan-rule"></span>
      </div>

      <p class="website">www.tiroengineering.org</p>
    </section>
  </main>
</body>
</html>
```